High Tech Real Estate Startup needs a business card

We are developing an innovative real estate marketing product based around advanced search and virtual reality.

We talk to people, we need business cards.

Target Market(s)

The target market is technology professionals and realtors.

Contact Information for Business Card

The information to be included will include

Name
Title
Phone Number
E-mail Address
www.zelquin.com

It should use simple iconography for each one of those fields.

Font styles to use
Other font styles liked:
• Co, Jubilat, Avenir

Colors

Designer to choose colors to be used in the design.

Requirements
Must have
• Clean aesthetic,
• Good use of negative space.
• It should use our company logo, shown in the attached file. It is able to use the negative of that logo (coloured font and white background) and I have attached other acceptable accent colours in a swatch file.
Should not have
• Should not be too busy
• No extraneous text (slogans, tag lines etc)

```html
<!DOCTYPE html>
<html lang="en">
<head>
<meta charset="UTF-8">
<title>Zelquin Business Card</title>
<link rel="stylesheet" href="https://fonts.googleapis.com/css2?family=Nunito+Sans:wght@400;600;700&display=swap">
<style>
  :root {
    --teal: #19b9bb;
    --card: #ffffff;
    --backdrop: #2b2b2d;
    --card-w: 620px;
    --card-h: 354px;
  }
  * { box-sizing: border-box; margin: 0; padding: 0; }
  html, body {
    width: 1200px;
    height: 880px;
    overflow: hidden;
    background: var(--backdrop);
    font-family: "Nunito Sans", "Avenir", sans-serif;
  }
  .canvas {
    position: relative;
    width: 1200px;
    height: 880px;
  }
  .card {
    position: absolute;
    width: var(--card-w);
    height: var(--card-h);
    background: var(--card);
    border-radius: 22px;
    overflow: hidden;
    box-shadow: 0 14px 30px rgba(0, 0, 0, 0.45);
  }
  .card::after {
    content: "";
    position: absolute;
    left: 0; right: 0; bottom: 0;
    height: 14px;
    background: var(--teal);
  }
  .card--back { left: 110px; top: 60px; }
  .card--front { left: 470px; top: 466px; }

  .wordmark {
    position: absolute;
    left: 0; right: 0;
    text-align: center;
    color: var(--teal);
    font-weight: 600;
    letter-spacing: 6px;
    line-height: 1;
  }
  .card--back .wordmark { top: 132px; font-size: 74px; }
  .card--front .wordmark { top: 66px; font-size: 68px; }

  .details {
    position: absolute;
    left: 0; right: 0;
    top: 214px;
    display: flex;
    justify-content: center;
    align-items: center;
    gap: 22px;
    color: var(--teal);
  }
  .person { text-align: right; }
  .person__name {
    font-size: 19px;
    font-weight: 700;
    letter-spacing: 0.5px;
    line-height: 1.1;
  }
  .person__title {
    font-size: 14px;
    font-weight: 400;
    line-height: 1.2;
  }
  .divider {
    width: 1px;
    height: 62px;
    background: var(--teal);
  }
  .contacts { list-style: none; }
  .contacts li {
    display: flex;
    align-items: center;
    gap: 8px;
    font-size: 14px;
    line-height: 1.45;
  }
  .contacts svg { width: 12px; height: 12px; fill: var(--teal); flex: none; }
</style>
</head>
<body>
<div class="canvas">
  <section class="card card--back">
    <div class="wordmark">ZELQUIN</div>
  </section>

  <section class="card card--front">
    <div class="wordmark">ZELQUIN</div>
    <div class="details">
      <div class="person">
        <div class="person__name">DARA VELKO</div>
        <div class="person__title">Manager</div>
      </div>
      <div class="divider"></div>
      <ul class="contacts">
        <li>
          <svg viewBox="0 0 24 24" aria-hidden="true"><path d="M6.6 10.8a15.1 15.1 0 0 0 6.6 6.6l2.2-2.2c.3-.3.7-.4 1-.2 1.1.4 2.3.6 3.6.6.6 0 1 .4 1 1V20c0 .6-.4 1-1 1A17 17 0 0 1 3 4c0-.6.4-1 1-1h3.5c.6 0 1 .4 1 1 0 1.3.2 2.5.6 3.6.1.3 0 .7-.2 1z"/></svg>
          555-014-2290
        </li>
        <li>
          <svg viewBox="0 0 24 24" aria-hidden="true"><path d="M2 5h20v14H2z M3.5 6.5 12 13l8.5-6.5" fill="none" stroke="#19b9bb" stroke-width="2.4"/></svg>
          hello@zelquin.com
        </li>
        <li>
          <svg viewBox="0 0 24 24" aria-hidden="true"><circle cx="12" cy="12" r="9.5" fill="none" stroke="#19b9bb" stroke-width="2"/><path d="M2.5 12h19M12 2.5c3 3 3 16 0 19M12 2.5c-3 3-3 16 0 19" fill="none" stroke="#19b9bb" stroke-width="1.6"/></svg>
          www.zelquin.com
        </li>
      </ul>
    </div>
  </section>
</div>
</body>
</html>
```